Business Card Design

We are looking for a business card designed for our landscaping company. We do landscaping installation & Maintenance Services. We would like to see designs that have basic landscaping in background. We also think it is important to have both of our names and phone numbers on the card. We need something that stands out a little whether it is shape of the card or thickness or design.

Business

Bramblewood Yardworks, bramblewoodyard@mailvista.net, Owen Platt 555-273-9104, Daniel Korbin 555-618-3927

```html
<!DOCTYPE html>
<html lang="en">
<head>
<meta charset="utf-8">
<title>Bramblewood Yardworks – Business Card</title>
<link href="https://fonts.googleapis.com/css2?family=Bodoni+Moda:wght@500;600&family=Open+Sans:wght@400&display=swap" rel="stylesheet">
<style>
  :root {
    --page-bg: #e6e2dc;
    --card-face: #eef0f1;
    --card-edge: #d6d9db;
    --ink: #1c1c1c;
    --rule: #2a2a2a;
    --leaf-green: #1f7a3a;
    --leaf-green-dark: #145a29;
    --swoosh: #111111;
    --email-tint: #e19a9a;
  }
  * { margin: 0; padding: 0; box-sizing: border-box; }
  html, body {
    width: 1200px; height: 970px; overflow: hidden;
    background: var(--page-bg);
  }
  .canvas { position: relative; width: 1200px; height: 970px; }
  .business-card {
    position: absolute; left: 100px; top: 185px;
    width: 1000px; height: 600px;
    border-radius: 30px; overflow: hidden;
    background: linear-gradient(160deg, #f7f8f9 0%, var(--card-face) 55%, #e3e6e8 100%);
    box-shadow: 0 0 0 1px var(--card-edge), 0 14px 34px rgba(0,0,0,0.12);
  }
  .card-art { position: absolute; inset: 0; }
  .company-name {
    position: absolute; top: 78px; left: 0; width: 100%;
    text-align: center;
    font-family: "Bodoni Moda", "Didot", serif; font-weight: 600;
    font-size: 62px; color: var(--ink); letter-spacing: -0.5px;
  }
  .title-rule {
    position: absolute; top: 189px; left: 106px; width: 806px;
    height: 2px; background: var(--rule);
  }
  .contact { position: absolute; top: 290px; }
  .contact--left { left: 134px; }
  .contact--right { left: 587px; }
  .contact-name {
    font-family: "Bodoni Moda", "Didot", serif; font-weight: 600;
    font-size: 43px; color: var(--ink); line-height: 1.2;
  }
  .contact-phone {
    display: flex; align-items: center; gap: 12px; margin-top: 8px;
    font-family: "Open Sans", Arial, sans-serif; font-size: 31px; color: var(--ink);
  }
  .phone-icon { width: 23px; height: 23px; flex: none; }
  .email {
    position: absolute; top: 515px; left: 0; width: 1010px; text-align: center;
    font-family: "Open Sans", Arial, sans-serif; font-size: 28px;
    color: var(--email-tint);
  }
</style>
</head>
<body>
<div class="canvas">
  <div class="business-card">
    <svg class="card-art" width="1000" height="600" viewBox="0 0 1000 600">
      <defs>
        <linearGradient id="band-green" x1="0" y1="0" x2="1" y2="0">
          <stop offset="0" stop-color="var(--leaf-green)"/>
          <stop offset="0.6" stop-color="var(--leaf-green)"/>
          <stop offset="1" stop-color="var(--leaf-green-dark)"/>
        </linearGradient>
      </defs>
      <path class="green-band" d="M0,540 C250,478 600,452 1000,498 L1000,600 L0,600 Z" fill="url(#band-green)"/>
      <path class="swoosh" d="M70,512 C330,440 700,430 1000,474 L1000,530 C760,470 420,462 70,512 Z" fill="var(--swoosh)"/>
      <path class="swoosh-highlight" d="M70,512 C420,462 760,470 1000,530" fill="none" stroke="#c9a58f" stroke-width="2"/>
    </svg>

    <h1 class="company-name">Bramblewood Yardworks</h1>
    <div class="title-rule"></div>

    <div class="contact contact--left">
      <div class="contact-name">Owen Platt</div>
      <div class="contact-phone">
        <svg class="phone-icon" viewBox="0 0 24 24"><rect width="24" height="24" fill="var(--ink)"/><path d="M8 4 L11 4 L12 8 L10 9.5 C11 12.5 12 14 14.5 15 L16 13 L20 14 L20 17.5 C20 18.5 19 19.5 17.5 19.2 C11 18 6 13 4.8 6.5 C4.6 5 5.5 4 7 4 Z" fill="#fff"/></svg>
        <span>555-273-9104</span>
      </div>
    </div>

    <div class="contact contact--right">
      <div class="contact-name">Daniel Korbin</div>
      <div class="contact-phone">
        <svg class="phone-icon" viewBox="0 0 24 24"><rect width="24" height="24" fill="var(--ink)"/><path d="M8 4 L11 4 L12 8 L10 9.5 C11 12.5 12 14 14.5 15 L16 13 L20 14 L20 17.5 C20 18.5 19 19.5 17.5 19.2 C11 18 6 13 4.8 6.5 C4.6 5 5.5 4 7 4 Z" fill="#fff"/></svg>
        <span>555-618-3927</span>
      </div>
    </div>

    <div class="email">bramblewoodyard@mailvista.net</div>
  </div>
</div>
</body>
</html>
```